IT Company requires new Business Card design.

Over the years we have had a few different business card designs. We are now due for new cards across the board for all staff. We felt this would be a good time to start fresh with a new design. Our traditional card simply had our details on the front, and a list of services on the back. We don't particularly need the list of services, we have had cards where the only thing on the rear of the card was our logo.
Feel free to be creative, we would like our tag line "Complete IT Management" to appear at some point, doesn't necessarily have to be with the logo.
I have attached samples and drafts of various previous cards we have used over the years.

```html
<!DOCTYPE html>
<html lang="en">
<head>
<meta charset="utf-8">
<title>Ridgeline Networks – Business Card</title>
<link href="https://fonts.googleapis.com/css2?family=Open+Sans:wght@400;600;800&display=swap" rel="stylesheet">
<style>
  :root {
    --page: #e4e4ea;
    --card-dark: #3b3b3d;
    --card-dark-2: #2c2c2e;
    --band-blue: #2470aa;
    --text-white: #ffffff;
    --text-silver: #d6d6d8;
    --divider: rgba(255,255,255,0.35);
  }
  * { margin: 0; padding: 0; box-sizing: border-box; }
  html, body {
    width: 1200px; height: 987px; overflow: hidden;
    background: var(--page);
    font-family: "Open Sans", Arial, sans-serif;
  }
  .card {
    position: absolute; left: 220px; width: 760px; height: 434px;
    border-radius: 22px; overflow: hidden;
    background: linear-gradient(160deg, var(--card-dark) 0%, var(--card-dark-2) 100%);
    box-shadow: 0 6px 18px rgba(0,0,0,0.18);
  }
  .card--front { top: 40px; }
  .card--back { top: 513px; }

  /* front */
  .brand {
    position: absolute; left: 0; right: 0; top: 42px; text-align: center;
  }
  .brand__name {
    display: inline-flex; align-items: center; gap: 14px;
    font-weight: 800; font-size: 46px; letter-spacing: 1px;
    color: var(--text-white); text-transform: uppercase; line-height: 1;
  }
  .brand__mark {
    width: 30px; height: 30px; background: var(--text-silver);
  }
  .brand__tagline {
    margin-top: 12px; font-size: 15px; letter-spacing: 6px;
    color: var(--text-silver); text-transform: uppercase;
  }
  .info-band {
    position: absolute; left: 0; right: 0; top: 168px; height: 186px;
    background: var(--band-blue);
    display: flex; align-items: center;
  }
  .person {
    width: 50%; text-align: right; padding-right: 34px;
    color: var(--text-white);
  }
  .person__name { font-weight: 800; font-size: 25px; }
  .person__role { font-size: 18px; margin-bottom: 8px; }
  .person__address { font-size: 17px; line-height: 1.35; }
  .band-divider {
    width: 1px; height: 140px; background: var(--divider);
  }
  .contacts {
    list-style: none; padding-left: 30px; color: var(--text-white);
    font-size: 17px; line-height: 1.6;
  }
  .contacts li { display: flex; align-items: center; gap: 10px; }
  .contacts svg { width: 16px; height: 16px; flex: none; }
  .footer-tagline {
    position: absolute; left: 0; right: 0; bottom: 26px; text-align: center;
    font-size: 18px; letter-spacing: 7px; color: var(--text-white);
    text-transform: uppercase;
  }

  /* back */
  .back-brand {
    position: absolute; left: 0; right: 0; top: 160px; text-align: center;
  }
  .back-brand .brand__name { font-size: 52px; }
  .back-url {
    position: absolute; left: 0; right: 0; bottom: 70px; text-align: center;
    font-size: 17px; color: var(--text-white);
  }
</style>
</head>
<body>

<section class="card card--front">
  <div class="brand">
    <div class="brand__name"><span class="brand__mark"></span>Ridgeline Networks</div>
    <div class="brand__tagline">Complete IT Management</div>
  </div>

  <div class="info-band">
    <div class="person">
      <div class="person__name">Daniel Hart</div>
      <div class="person__role">Operation Manager</div>
      <div class="person__address">Unit 4 18 Harbour Road<br>Coogee WA 6166</div>
    </div>
    <div class="band-divider"></div>
    <ul class="contacts">
      <li><svg viewBox="0 0 16 16"><path fill="#fff" d="M3.5 1l2.5 3-1.5 1.8a8 8 0 0 0 5.7 5.7L12 10l3 2.5-1.6 2.3C7.5 15 1 8.5 1.2 2.6z"/></svg>08 9300 4812</li>
      <li><svg viewBox="0 0 16 16"><rect x="4" y="1" width="8" height="14" rx="1.5" fill="#fff"/><rect x="5.5" y="3" width="5" height="7" fill="#2470aa"/></svg>0412 558 907</li>
      <li><svg viewBox="0 0 16 16"><rect x="4" y="1" width="8" height="5" fill="#fff"/><rect x="1" y="6" width="14" height="7" rx="1" fill="#fff"/><rect x="4" y="10" width="8" height="5" fill="#fff" stroke="#2470aa"/></svg>08 9300 4812</li>
      <li><svg viewBox="0 0 16 16"><rect x="1" y="3" width="14" height="10" rx="1" fill="#fff"/><path d="M1.5 3.5L8 9l6.5-5.5" stroke="#2470aa" stroke-width="1.4" fill="none"/></svg>daniel@ridgelinenetworks.com.au</li>
      <li><svg viewBox="0 0 16 16"><circle cx="8" cy="8" r="6.5" fill="none" stroke="#fff" stroke-width="1.4"/><ellipse cx="8" cy="8" rx="2.8" ry="6.5" fill="none" stroke="#fff" stroke-width="1.2"/><path d="M1.5 8h13" stroke="#fff" stroke-width="1.2"/></svg>www.ridgelinenetworks.com.au</li>
    </ul>
  </div>

  <div class="footer-tagline">Complete IT Management</div>
</section>

<section class="card card--back">
  <div class="back-brand">
    <div class="brand__name"><span class="brand__mark"></span>Ridgeline Networks</div>
  </div>
  <div class="back-url">www.ridgelinenetworks.com.au</div>
</section>

</body>
</html>
```